Professional & attention grabbing.

A business card design, front and back. I already have a logo I will attach, but I am open to something new as well.
Things to include:
Name:
Title:
Phone:
Email:
Wanting something that is professional but attention grabbing.
Also we do a lot of work using drones on natural gas pipelines (leading the future)if you want to include any of that. I'm open to ideas.
Target Market(s)
Natural gas transmission industry / greenhouse gas mitigation industry
Industry/Entity Type
Business
Colors
Designer to choose colors to be used in the design.
Look and feel
Each slider illustrates characteristics of the customer's brand and the style your logo design should communicate.

```html
<!DOCTYPE html>
<html lang="en">
<head>
<meta charset="utf-8">
<title>Kestrel Line Inspections — Business Card</title>
<link href="https://fonts.googleapis.com/css2?family=Open+Sans:wght@400;600;700;800&display=swap" rel="stylesheet">
<style>
  :root {
    --backdrop: #5e4b3b;
    --brand-red: #c21f26;
    --charcoal: #3a3a3d;
    --paper: #ffffff;
    --muted: #f2f2f2;
  }
  html, body {
    margin: 0;
    padding: 0;
    width: 1200px;
    height: 987px;
    overflow: hidden;
    background: var(--backdrop);
    font-family: "Open Sans", Arial, sans-serif;
  }
  .canvas {
    position: relative;
    width: 1200px;
    height: 987px;
  }
  .card {
    position: absolute;
    left: 293px;
    width: 615px;
    height: 351px;
    overflow: hidden;
    box-shadow: 0 3px 8px rgba(0,0,0,0.35);
  }

  /* Front */
  .card--front {
    top: 130px;
    background: var(--paper);
  }
  .front__topband {
    position: absolute;
    left: 0; top: 0;
    width: 100%;
    height: 11px;
    background: var(--brand-red);
  }
  .brand {
    position: absolute;
    left: 64px;
    top: 72px;
    display: flex;
    align-items: center;
    gap: 16px;
  }
  .brand__square {
    width: 88px;
    height: 88px;
    background: var(--brand-red);
  }
  .brand__name {
    color: var(--charcoal);
    font-weight: 800;
    line-height: 1;
  }
  .brand__name-main {
    display: block;
    font-size: 52px;
    letter-spacing: -1px;
  }
  .brand__name-sub {
    display: block;
    font-size: 12px;
    letter-spacing: 0.4px;
    margin-top: 6px;
  }
  .front__infoband {
    position: absolute;
    left: 0; top: 215px;
    width: 100%;
    height: 136px;
    background: var(--charcoal);
  }
  .person {
    position: absolute;
    left: 64px;
    top: 42px;
  }
  .person__name {
    margin: 0;
    color: var(--brand-red);
    font-size: 21px;
    font-weight: 600;
    letter-spacing: 0.2px;
  }
  .person__title {
    margin: 2px 0 0;
    color: var(--paper);
    font-size: 16px;
  }
  .contact {
    position: absolute;
    left: 360px;
    top: 30px;
    margin: 0;
    padding: 0;
    list-style: none;
  }
  .contact__item {
    display: flex;
    align-items: center;
    gap: 9px;
    height: 23.5px;
    color: var(--paper);
    font-size: 15.5px;
  }
  .contact__icon {
    width: 14px;
    height: 14px;
    fill: var(--brand-red);
    flex: none;
  }

  /* Back */
  .card--back {
    top: 505px;
    background: var(--brand-red);
  }
  .back__disc {
    position: absolute;
    left: 345px;
    top: 40px;
    width: 420px;
    height: 420px;
    border-radius: 50%;
    background: var(--charcoal);
  }
  .back__brand {
    position: absolute;
    left: 21px;
    top: 18px;
    color: var(--paper);
    font-weight: 800;
    line-height: 1;
  }
  .back__brand-main {
    display: block;
    font-size: 74px;
    letter-spacing: -2px;
  }
  .back__brand-sub {
    display: block;
    font-size: 16px;
    margin-top: 10px;
    letter-spacing: 0.3px;
  }
  .back__web {
    position: absolute;
    left: 21px;
    top: 156px;
    color: var(--paper);
    font-size: 14px;
    font-style: italic;
    letter-spacing: 2.6px;
  }
</style>
</head>
<body>
<main class="canvas">

  <section class="card card--front" aria-label="Business card front">
    <div class="front__topband"></div>

    <div class="brand">
      <div class="brand__square"></div>
      <div class="brand__name">
        <span class="brand__name-main">KESTREL</span>
        <span class="brand__name-sub">LINE INSPECTIONS</span>
      </div>
    </div>

    <div class="front__infoband">
      <div class="person">
        <p class="person__name">DANIEL REYES</p>
        <p class="person__title">CEO/Founder</p>
      </div>

      <ul class="contact">
        <li class="contact__item">
          <svg class="contact__icon" viewBox="0 0 24 24" aria-hidden="true"><path d="M6.6 10.8a15.1 15.1 0 0 0 6.6 6.6l2.2-2.2c.3-.3.7-.4 1-.2 1.1.4 2.3.6 3.6.6.6 0 1 .4 1 1V20c0 .6-.4 1-1 1C10.6 21 3 13.4 3 4c0-.6.4-1 1-1h3.5c.6 0 1 .4 1 1 0 1.3.2 2.5.6 3.6.1.3 0 .7-.2 1z"/></svg>
          555 014 2738
        </li>
        <li class="contact__item">
          <svg class="contact__icon" viewBox="0 0 24 24" aria-hidden="true"><path d="M2 5h20v14H2z M3.5 6.5 12 12.5l8.5-6z" fill-rule="evenodd"/></svg>
          hello@kestrelline.com
        </li>
        <li class="contact__item">
          <svg class="contact__icon" viewBox="0 0 24 24" aria-hidden="true"><circle cx="12" cy="12" r="10"/></svg>
          www.kestrelline.com
        </li>
      </ul>
    </div>
  </section>

  <section class="card card--back" aria-label="Business card back">
    <div class="back__disc"></div>
    <div class="back__brand">
      <span class="back__brand-main">KESTREL</span>
      <span class="back__brand-sub">LINE INSPECTIONS</span>
    </div>
    <div class="back__web">www.kestrelline.com</div>
  </section>

</main>
</body>
</html>
```